Redesign of Medical App for Patients

• The Designer’s task is to provide a new fully-responsive design for our apps, and then code it using only basic html and CSS.
• Your design will be incorporated into our existing REACT native app.

Target Market(s)

Medical Patients

Industry/Entity Type

Medical

Coding

Coded - Design and coding required

Number of Pages Required

5+ page

Requirements
Must have
• Short list candidates will receive detailed briefing
Nice to have
• detailed briefing contains some of our ideas.

```html
<!DOCTYPE html>
<html lang="en">
<head>
<meta charset="utf-8">
<title>CareGuide – Patient App Screens</title>
<link rel="stylesheet" href="https://fonts.googleapis.com/css2?family=Bebas+Neue&family=Nunito+Sans:wght@400;600&display=swap">
<style>
:root{
  --board:#e3e4e6;
  --white:#ffffff;
  --paper:#f2f2f2;
  --ink:#1f2a35;
  --blue:#2b86b8;
  --photo-a:#3a93c4;
  --photo-b:#2a78a8;
  --placeholder:#dcdcdc;
  --shadow:rgba(0,0,0,.08);
}
*{box-sizing:border-box;margin:0;padding:0}
html,body{width:714px;height:1200px;overflow:hidden;background:var(--board);font-family:"Nunito Sans",sans-serif;color:var(--ink)}
.board{position:relative;width:714px;height:1200px}
.screen{position:absolute;width:295px;height:525px;background:var(--paper);overflow:hidden}
.screen--mini{left:87px;top:107px;width:211px;height:440px;border-radius:26px;box-shadow:0 0 0 1px #cfd1d4}
.screen--recovery{left:380px;top:52px;background:var(--photo-b)}
.screen--about{left:48px;top:614px}
.screen--procedure{left:380px;top:614px}

.app-bar{position:absolute;left:0;top:0;width:100%;height:40px;background:var(--white);display:flex;align-items:center;padding:0 14px;gap:10px;z-index:2}
.app-bar .menu,.app-bar .search{width:16px;height:16px;flex:none}
.brand{display:flex;align-items:center;gap:6px;font-weight:600;font-size:16px;letter-spacing:-.2px;color:var(--blue);white-space:nowrap}
.brand .dot{width:22px;height:22px;border-radius:50%;background:var(--blue);flex:none}
.app-bar .search{margin-left:auto}
.screen--mini .app-bar{height:55px;padding:18px 10px 0;gap:7px}
.screen--mini .brand{font-size:11.5px;gap:4px}
.screen--mini .brand .dot{width:16px;height:16px}
.screen--mini .menu,.screen--mini .search{width:12px;height:12px}

.photo{position:absolute;left:0;width:100%}
.photo--recovery{top:40px;height:485px;background:linear-gradient(160deg,var(--photo-a),var(--photo-b) 70%,#3d8ec0)}
.photo--procedure{top:40px;height:287px;background:linear-gradient(135deg,#4aa3d0,var(--photo-a) 50%,var(--photo-b))}
.hero-title{position:absolute;left:0;width:100%;text-align:center;font-family:"Bebas Neue",sans-serif;font-weight:400;color:var(--white);font-size:23px;letter-spacing:.5px;z-index:1}

.section-title{position:absolute;left:0;width:100%;text-align:center;font-family:"Bebas Neue",sans-serif;font-weight:400;font-size:22px;letter-spacing:.2px}
.section-title em{font-style:normal;color:var(--blue)}
.illustration{position:absolute;background:var(--placeholder);border-radius:4px}

.accordion{position:absolute;list-style:none}
.accordion li{display:flex;align-items:center;justify-content:space-between;background:var(--white);box-shadow:0 1px 3px var(--shadow);padding:0 14px 0 15px;white-space:nowrap}
.accordion svg{width:11px;height:11px;flex:none;margin-left:6px}
.accordion--large{left:16px;width:270px;font-size:12px}
.accordion--large li{height:36px}
.accordion--recovery{top:174px}
.accordion--recovery li+li{margin-top:10px}
.accordion--procedure{top:356px}
.accordion--procedure li+li{margin-top:18px}
.accordion--about{left:8px;top:361px;width:280px;font-size:10.5px}
.accordion--about li{height:29px;padding:0 12px}
.accordion--about li+li{margin-top:10px}
.accordion--mini{left:3px;top:284px;width:205px;font-size:6.4px}
.accordion--mini li{height:23px;padding:0 8px 0 10px}
.accordion--mini li+li{margin-top:6px}
.accordion--mini svg{width:8px;height:8px}
</style>
</head>
<body>
<svg width="0" height="0" style="position:absolute">
  <defs>
    <symbol id="i-menu" viewBox="0 0 16 16"><path d="M1 3h14M1 8h11M1 13h14" stroke="#1f2a35" stroke-width="2" stroke-linecap="round"/></symbol>
    <symbol id="i-search" viewBox="0 0 16 16"><circle cx="6.5" cy="6.5" r="5" fill="none" stroke="#1f2a35" stroke-width="2"/><path d="M10.3 10.3L15 15" stroke="#1f2a35" stroke-width="2" stroke-linecap="round"/></symbol>
    <symbol id="i-chevron" viewBox="0 0 12 12"><path d="M2 4l4 4 4-4" fill="none" stroke="#1f2a35" stroke-width="1.6" stroke-linecap="round" stroke-linejoin="round"/></symbol>
  </defs>
</svg>

<main class="board">

  <section class="screen screen--mini" aria-label="About procedure, compact view">
    <header class="app-bar">
      <svg class="menu"><use href="#i-menu"/></svg>
      <span class="brand"><span class="dot"></span>CAREGUIDE</span>
      <svg class="search"><use href="#i-search"/></svg>
    </header>
    <h2 class="section-title" style="top:74px;font-size:15px">About <em>Procedure</em></h2>
    <div class="illustration" role="img" aria-label="Labelled anatomical drawing of the liver, gallbladder and common bile duct" style="left:27px;top:116px;width:158px;height:135px"></div>
    <ul class="accordion accordion--mini">
      <li>Is it too late to prevent gallbladder disease?<svg><use href="#i-chevron"/></svg></li>
      <li>What will happen if I don't have this procedure?<svg><use href="#i-chevron"/></svg></li>
      <li>Are there alternative solutions?<svg><use href="#i-chevron"/></svg></li>
      <li>What are the risks of this procedure?<svg><use href="#i-chevron"/></svg></li>
    </ul>
  </section>

  <section class="screen screen--recovery" aria-label="Recovery">
    <header class="app-bar">
      <svg class="menu"><use href="#i-menu"/></svg>
      <span class="brand"><span class="dot"></span>CAREGUIDE</span>
      <svg class="search"><use href="#i-search"/></svg>
    </header>
    <div class="photo photo--recovery" role="img" aria-label="Blue-tinted photo of a hospital recovery ward with nurses and a patient resting"></div>
    <h2 class="hero-title" style="top:66px">Recovery</h2>
    <ul class="accordion accordion--large accordion--recovery">
      <li>When do I leave the Hospital?<svg><use href="#i-chevron"/></svg></li>
      <li>Waking up<svg><use href="#i-chevron"/></svg></li>
      <li>Pain management<svg><use href="#i-chevron"/></svg></li>
      <li>Same-day Discharge<svg><use href="#i-chevron"/></svg></li>
      <li>Ready to leave<svg><use href="#i-chevron"/></svg></li>
    </ul>
  </section>

  <section class="screen screen--about" aria-label="About procedure">
    <header class="app-bar">
      <svg class="menu"><use href="#i-menu"/></svg>
      <span class="brand"><span class="dot"></span>CAREGUIDE</span>
      <svg class="search"><use href="#i-search"/></svg>
    </header>
    <h2 class="section-title" style="top:75px">About <em>Procedure</em></h2>
    <div class="illustration" role="img" aria-label="Labelled anatomical drawing of the liver, gallbladder and common bile duct" style="left:36px;top:130px;width:222px;height:190px"></div>
    <ul class="accordion accordion--about">
      <li>Is it too late to prevent gallbladder disease?<svg><use href="#i-chevron"/></svg></li>
      <li>What will happen if I don't have this procedure?<svg><use href="#i-chevron"/></svg></li>
      <li>Are there alternative solutions?<svg><use href="#i-chevron"/></svg></li>
      <li>What are the risks of this procedure?<svg><use href="#i-chevron"/></svg></li>
    </ul>
  </section>

  <section class="screen screen--procedure" aria-label="Procedure">
    <header class="app-bar">
      <svg class="menu"><use href="#i-menu"/></svg>
      <span class="brand"><span class="dot"></span>CAREGUIDE</span>
      <svg class="search"><use href="#i-search"/></svg>
    </header>
    <div class="photo photo--procedure" role="img" aria-label="Blue-tinted photo of a doctor in a white coat talking with a patient across a desk"></div>
    <h2 class="hero-title" style="top:58px">Procedure</h2>
    <ul class="accordion accordion--large accordion--procedure">
      <li>Preparation<svg><use href="#i-chevron"/></svg></li>
      <li>What Happens?<svg><use href="#i-chevron"/></svg></li>
      <li>Immediately after<svg><use href="#i-chevron"/></svg></li>
    </ul>
  </section>

</main>
</body>
</html>
```